Business cards for Harbourline Supply Pty Ltd that import building products into Australia from China
Target Market(s)
Business to Business
Industry/Entity Type
Business
Contact Information for Business Card
Front: Logo and Business Name
Rear:
Desmond Varrick
General Manager
Mobile: 0427 561 394
email: dessie@harbourlinesupply.com.au
alternative email: dessie@outbackworks.com.au
web: www.harbourlinesupply.com.au
Adelaide, Brisbane and Darwin
Colors
ec1f27
fbee3d

```html
<!DOCTYPE html>
<html lang="en">
<head>
<meta charset="utf-8">
<title>Harbourline Supply Pty Ltd — Business Cards</title>
<link href="https://fonts.googleapis.com/css2?family=Montserrat:wght@400;500;600;700&display=swap" rel="stylesheet">
<style>
  :root {
    --brand-red: #ec1f27;
    --brand-yellow: #fbee3d;
    --card-black: #050505;
    --text-white: #f2f2f2;
    --backdrop: #3a3a3a;
  }
  * { box-sizing: border-box; margin: 0; padding: 0; }
  html, body {
    width: 1200px; height: 864px; overflow: hidden;
    background: var(--backdrop);
    font-family: "Montserrat", sans-serif;
  }
  .sheet {
    width: 1200px; height: 864px;
    display: flex; flex-direction: column;
    align-items: center; justify-content: center; gap: 56px;
  }
  .card {
    position: relative;
    width: 600px; height: 343px;
    background: var(--card-black);
    border-radius: 22px;
    overflow: hidden;
    box-shadow: 0 14px 30px rgba(0,0,0,0.45);
  }
  .brand-mark {
    display: flex; align-items: center; gap: 14px;
  }
  .brand-mark__dot {
    width: 18px; height: 18px; border-radius: 50%;
    background: var(--brand-yellow); flex: none;
  }
  .brand-mark__name {
    color: var(--brand-red);
    font-weight: 700;
    text-transform: uppercase;
    line-height: 1.05;
    letter-spacing: 1px;
  }
  /* front */
  .card--front .brand-mark {
    position: absolute; left: 0; right: 0; top: 112px;
    justify-content: center;
  }
  .card--front .brand-mark__name { font-size: 30px; }
  .card--front .cities {
    position: absolute; left: 0; right: 0; top: 236px;
    text-align: center; color: var(--text-white);
    font-size: 13px; font-weight: 500; letter-spacing: 0.5px;
  }
  .cities__sep {
    display: inline-block; width: 5px; height: 5px; border-radius: 50%;
    background: var(--brand-red); margin: 0 7px; vertical-align: middle;
  }
  /* back */
  .card--back .brand-mark {
    position: absolute; left: 44px; top: 118px; width: 230px;
  }
  .card--back .brand-mark__name { font-size: 21px; }
  .divider {
    position: absolute; left: 292px; top: 52px;
    width: 1.5px; height: 150px; background: var(--brand-red);
  }
  .contact {
    position: absolute; left: 314px; top: 52px; color: var(--text-white);
  }
  .contact__name {
    color: var(--brand-red); font-size: 22px; font-weight: 600;
  }
  .contact__role {
    font-size: 13px; font-weight: 500; margin-top: 2px;
  }
  .contact__list { list-style: none; margin-top: 16px; }
  .contact__item {
    display: flex; align-items: center; gap: 9px;
    font-size: 12.5px; font-weight: 500; line-height: 21px;
  }
  .contact__icon { width: 13px; height: 13px; flex: none; }
  .swoosh { position: absolute; left: 0; bottom: 0; width: 600px; height: 140px; }
</style>
</head>
<body>
<main class="sheet">
  <section class="card card--front" aria-label="Card front">
    <div class="brand-mark">
      <span class="brand-mark__dot"></span>
      <span class="brand-mark__name">Harbourline Supply<br>Pty Ltd</span>
    </div>
    <p class="cities">Adelaide<span class="cities__sep"></span>Brisbane<span class="cities__sep"></span>Darwin</p>
  </section>

  <section class="card card--back" aria-label="Card back">
    <div class="brand-mark">
      <span class="brand-mark__dot"></span>
      <span class="brand-mark__name">Harbourline Supply<br>Pty Ltd</span>
    </div>
    <div class="divider"></div>
    <div class="contact">
      <h1 class="contact__name">Desmond Varrick</h1>
      <p class="contact__role">General Manager</p>
      <ul class="contact__list">
        <li class="contact__item">
          <svg class="contact__icon" viewBox="0 0 14 14"><rect x="3.5" y="1" width="7" height="12" rx="1.2" fill="none" stroke="#fbee3d" stroke-width="1.4"/><circle cx="7" cy="11" r="0.8" fill="#fbee3d"/></svg>
          0427 561 394
        </li>
        <li class="contact__item">
          <svg class="contact__icon" viewBox="0 0 14 14"><rect x="1" y="3" width="12" height="8" fill="#fbee3d"/><path d="M1 3 L7 8 L13 3" fill="none" stroke="#050505" stroke-width="1.2"/></svg>
          dessie@harbourlinesupply.com.au
        </li>
        <li class="contact__item">
          <svg class="contact__icon" viewBox="0 0 14 14"><rect x="1" y="3" width="12" height="8" fill="#fbee3d"/><path d="M1 3 L7 8 L13 3" fill="none" stroke="#050505" stroke-width="1.2"/></svg>
          dessie@outbackworks.com.au
        </li>
        <li class="contact__item">
          <svg class="contact__icon" viewBox="0 0 14 14" fill="none" stroke="#fbee3d" stroke-width="1.2"><circle cx="7" cy="7" r="5.8"/><ellipse cx="7" cy="7" rx="2.5" ry="5.8"/><path d="M1.2 7 H12.8 M2 4 H12 M2 10 H12"/></svg>
          www.harbourlinesupply.com.au
        </li>
      </ul>
    </div>
    <svg class="swoosh" viewBox="0 0 600 140" preserveAspectRatio="none" aria-hidden="true">
      <path d="M0 118 C120 60 260 60 600 14 L600 30 C300 80 140 70 0 128 Z" fill="#fbee3d"/>
      <path d="M0 128 C140 70 300 84 600 26 L600 140 L0 140 Z" fill="#ec1f27"/>
    </svg>
  </section>
</main>
</body>
</html>
```